Business Card Design

We need a business card designed for our new company. Prefer a black card with white logo & writing.

Contact Information for Business Card

Ted Galloway, address: 7-4812 Fernhollow Road, Abbotsford, BC, V3K 8R2, Office Phone: 604-712-3390, Cell: 604-947-2164, Email: ted@resinworkshub.ca

Colors

Designer to choose only greyscale colors for use in the design.

```html
<!DOCTYPE html>
<html lang="en">
<head>
<meta charset="utf-8">
<title>Resin Works Hub – Business Card</title>
<link rel="stylesheet" href="https://fonts.googleapis.com/css2?family=Montserrat:wght@400;500;700&display=swap">
<style>
  :root {
    --backdrop: #222222;
    --card-black: #000000;
    --ink-white: #ffffff;
    --mid-grey: #808080;
    --icon-ink: #000000;
  }
  * { margin: 0; padding: 0; box-sizing: border-box; }
  html, body { width: 1200px; height: 900px; overflow: hidden; }
  body {
    background: var(--backdrop);
    font-family: "Montserrat", Arial, sans-serif;
    color: var(--ink-white);
    position: relative;
  }
  .card {
    position: absolute;
    top: 192px;
    width: 296px;
    height: 518px;
    background: var(--card-black);
    overflow: hidden;
  }
  .card--front { left: 292px; }
  .card--back { left: 614px; }

  .brand-name {
    position: absolute;
    top: 78px;
    left: 0;
    width: 100%;
    text-align: center;
    font-weight: 700;
    font-size: 27px;
    line-height: 31px;
    letter-spacing: 0.5px;
    color: var(--ink-white);
  }

  .contact-block {
    position: absolute;
    top: 246px;
    left: 0;
    width: 100%;
    text-align: center;
  }
  .person-name {
    font-weight: 700;
    font-size: 19px;
    line-height: 22px;
    letter-spacing: 0.3px;
  }
  .person-role {
    font-weight: 400;
    font-size: 13px;
    line-height: 18px;
    margin-top: 1px;
  }
  .divider {
    width: 34px;
    height: 1.5px;
    background: var(--ink-white);
    margin: 12px auto 13px;
  }
  .address {
    font-size: 13.5px;
    line-height: 18px;
  }
  .icon-row {
    display: flex;
    justify-content: center;
    gap: 6px;
    margin-top: 21px;
  }
  .icon {
    width: 19px;
    height: 19px;
    border-radius: 50%;
    background: var(--ink-white);
    display: flex;
    align-items: center;
    justify-content: center;
  }
  .icon svg { width: 13px; height: 13px; }
  .contact-lines {
    margin-top: 7px;
    font-size: 13.5px;
    line-height: 18px;
  }

  .mountain-art {
    position: absolute;
    top: 230px;
    left: 0;
    width: 100%;
    height: 228px;
    background: linear-gradient(180deg, var(--mid-grey) 0%, #b8b8b8 45%, var(--ink-white) 100%);
  }
  .back-footer {
    position: absolute;
    top: 458px;
    left: 0;
    width: 100%;
    height: 60px;
    background: var(--ink-white);
  }
  .web-address {
    position: absolute;
    top: 472px;
    left: 0;
    width: 100%;
    text-align: center;
    font-size: 12px;
    letter-spacing: 2.4px;
    color: var(--card-black);
    font-weight: 500;
  }
  .web-address strong { font-weight: 700; }
</style>
</head>
<body>

  <section class="card card--front" aria-label="Card front">
    <div class="brand-name">RESIN WORKS<br>HUB</div>

    <div class="contact-block">
      <p class="person-name">TED GALLOWAY</p>
      <p class="person-role">President</p>
      <div class="divider"></div>
      <p class="address">7-4812 Fernhollow Road<br>Abbotsford, BC, V3K 8R2</p>

      <div class="icon-row">
        <span class="icon" aria-label="Office phone">
          <svg viewBox="0 0 24 24"><path fill="var(--icon-ink)" d="M6.6 10.8a15 15 0 0 0 6.6 6.6l2.2-2.2a1 1 0 0 1 1-.25 11.4 11.4 0 0 0 3.6.57 1 1 0 0 1 1 1V20a1 1 0 0 1-1 1A17 17 0 0 1 3 4a1 1 0 0 1 1-1h3.5a1 1 0 0 1 1 1c0 1.25.2 2.45.57 3.57a1 1 0 0 1-.25 1z"/></svg>
        </span>
        <span class="icon" aria-label="Cell phone">
          <svg viewBox="0 0 24 24"><rect x="7" y="2" width="10" height="20" rx="2" fill="none" stroke="var(--icon-ink)" stroke-width="2"/><circle cx="12" cy="18" r="1.2" fill="var(--icon-ink)"/></svg>
        </span>
        <span class="icon" aria-label="Email">
          <svg viewBox="0 0 24 24"><rect x="3" y="5" width="18" height="14" rx="2" fill="var(--icon-ink)"/><path d="M4 7l8 6 8-6" fill="none" stroke="var(--ink-white)" stroke-width="1.6"/></svg>
        </span>
        <span class="icon" aria-label="Website">
          <svg viewBox="0 0 24 24" fill="none" stroke="var(--icon-ink)" stroke-width="1.6"><circle cx="12" cy="12" r="9"/><ellipse cx="12" cy="12" rx="4" ry="9"/><path d="M3 12h18M5 7h14M5 17h14"/></svg>
        </span>
      </div>

      <div class="contact-lines">
        <p>604-712-3390</p>
        <p>604-947-2164</p>
        <p>ted@resinworkshub.ca</p>
        <p>resinworkshub.ca</p>
      </div>
    </div>
  </section>

  <section class="card card--back" aria-label="Card back">
    <div class="brand-name">RESIN WORKS<br>HUB</div>
    <div class="mountain-art" role="img" aria-label="Stylised grey and white mountain peak illustration"></div>
    <div class="back-footer"></div>
    <p class="web-address">www.<strong>resinworkshub</strong>.ca</p>
  </section>

</body>
</html>
```